Informational Site for Advanced Chemistry R&D

The company develops oxidation chemistry for air, water, fuel pollution controls. The site has been prototyped at www.velquaresearch.example. Take a look. Now, the task is to design it for eye-catching beauty with use of color, on-page scroll-driven color transition and parallax effects. Should capture the themes: high technology, wow it's beautiful, modern, uncluttered, clean urban environment.

Target Market(s)

China Environmentally Conscious Government and Industry,

Industry/Entity Type

It Company

Number of Pages Required

3 page

Font styles to use
Sans Serif

Requirements
Must have
• Parallax effects, desktop compatible, Rich, Modern, Simple, Graphic
Nice to have
• Mobile Phone Compatible
Should not have
• Flash, or anything that is slow to load or requires high bandwidth

```html
<!DOCTYPE html>
<html lang="en">
<head>
<meta charset="utf-8">
<title>Velqua — Advanced Oxidation Science</title>
<link rel="stylesheet" href="https://fonts.googleapis.com/css2?family=Quicksand:wght@500;600;700&family=Open+Sans:wght@400;600&display=swap">
<style>
:root{
  --teal:#2bb3b1;
  --teal-dark:#1e9a9b;
  --blue:#1b72c0;
  --navy:#1f4f78;
  --green:#8bbd3c;
  --ink:#333b44;
  --muted:#8a9299;
  --pale:#eef3f6;
  --white:#ffffff;
}
*{box-sizing:border-box;margin:0;padding:0}
html,body{width:1200px;height:4235px;overflow:hidden}
body{position:relative;font-family:"Open Sans",Arial,sans-serif;color:var(--ink);background:var(--white)}
h1,h2,h3,.brand,.nav a{font-family:"Quicksand","Open Sans",sans-serif}
.abs{position:absolute}

/* header / hero */
.hero{position:absolute;left:0;top:0;width:1200px;height:700px;overflow:hidden}
.hero-photo{position:absolute;inset:0;background:linear-gradient(180deg,#dfe7ee 0%,#eef2f5 45%,#d4dde4 70%,#e9eef2 100%)}
.brand{display:flex;align-items:center;gap:10px;font-weight:700;font-size:34px;color:var(--teal)}
.brand .dot{width:22px;height:22px;border-radius:50%;background:var(--teal)}
.site-brand{left:82px;top:52px}
.nav{position:absolute;top:62px;left:0;width:1200px;height:30px}
.nav a{position:absolute;font-size:17px;font-weight:600;color:#4a5259;text-decoration:none;transform:translateX(-50%)}
.nav .active{color:var(--teal);border:2px solid var(--teal);border-radius:30px;padding:8px 14px;top:-10px}
.hero-title{left:0;width:1200px;top:352px;text-align:center;font-size:48px;font-weight:600;color:var(--teal);line-height:1.1}
.hero-sub{left:0;width:1200px;top:404px;text-align:center;font-size:33px;font-weight:600;color:var(--teal)}
.scroll-cue{left:582px;top:598px;width:36px;height:36px;border:2px solid var(--teal);border-radius:50%}

/* about */
.about{position:absolute;left:0;top:664px;width:1200px;height:644px;background:linear-gradient(180deg,#2f7fa8 0%,#3a7597 50%,#586c7c 100%)}
.about h2{left:90px;top:170px;font-size:44px;font-weight:600;color:var(--white)}
.about h2 span{color:#5fd3d8}
.about-copy{left:90px;top:256px;width:620px;font-size:14.5px;line-height:1.7;color:#e7f1f6}
.about-copy p{margin-bottom:22px}
.photo-circle{position:absolute;border-radius:50%;border:7px solid var(--teal)}

/* section headings */
.sec-title{left:0;width:1200px;text-align:center;font-size:40px;font-weight:600;color:var(--blue)}
.sec-title span{color:var(--teal)}
.sec-lead{left:0;width:1200px;text-align:center;font-size:14.5px;color:var(--muted)}

/* solutions */
.solution{position:absolute;width:300px;text-align:center}
.sol-icon{width:124px;height:124px;margin:0 auto}
.solution h3{margin-top:52px;font-size:27px;font-weight:700;color:var(--blue)}
.solution p{margin:18px auto 0;width:270px;font-size:13.5px;line-height:1.6;color:var(--muted)}
.read-more{display:block;margin-top:14px;font-size:13px;color:var(--green);text-decoration:none}
.read-more::before{content:"";display:block;margin:0 auto 6px;width:12px;height:12px;border-radius:50%;border:2px solid var(--green)}

/* advanced oxidation */
.tech{position:absolute;left:0;top:2019px;width:1200px;height:599px;background:linear-gradient(135deg,#1fa7a7 0%,#44c0bd 50%,#6cd0cc 100%)}
.tech-photo{left:85px;top:113px;width:390px;height:381px;background:linear-gradient(160deg,#9fb7c6 0%,#4d6b85 55%,#233f5c 100%)}
.tech h2{left:518px;top:160px;font-size:42px;font-weight:600;color:var(--blue)}
.tech h2 span{color:var(--white)}
.tech-copy{left:520px;top:236px;width:600px;font-size:14.5px;line-height:1.75;color:var(--white)}
.tech-copy ul{list-style:none;margin:18px 0}
.tech-copy li{position:relative;padding-left:22px}
.tech-copy li::before{content:"";position:absolute;left:2px;top:8px;width:9px;height:9px;background:var(--white);transform:rotate(45deg)}

/* products */
.product{position:absolute;width:260px;text-align:center}
.prod-photo{width:180px;height:180px;margin:0 auto;border-radius:50%;border:6px solid var(--teal)}
.product h3{margin-top:22px;font-size:24px;font-weight:700;color:var(--navy)}
.product .full{margin-top:6px;font-size:13px;line-height:1.4;color:var(--teal);padding-bottom:14px;border-bottom:1px solid #d9dee2;width:210px;margin-left:auto;margin-right:auto}
.product p{margin-top:12px;font-size:13.5px;line-height:1.6;color:var(--muted)}

/* partners */
.partners{position:absolute;left:0;top:3327px;width:1200px;height:302px;background:var(--blue)}
.partner{position:absolute;width:240px;text-align:center;top:70px}
.partner .mark{height:90px;display:flex;align-items:center;justify-content:center;gap:10px;font-family:"Quicksand",sans-serif;font-weight:700;font-size:24px;color:var(--white)}
.partner .seal{width:90px;height:90px;border-radius:50%;border:3px solid var(--white)}
.partner .ring{width:18px;height:18px;border-radius:50%;background:var(--white)}
.partner p{margin-top:14px;font-size:13.5px;line-height:1.4;color:#6fd1d6}

/* contact */
.map{position:absolute;left:0;top:3629px;width:1200px;height:520px;background:linear-gradient(180deg,#eceeef 0%,#e4e7e9 100%)}
.card{position:absolute;left:376px;top:3657px;width:443px;height:395px;background:var(--white);box-shadow:0 4px 18px rgba(0,0,0,.12);text-align:center}
.card .brand{justify-content:center;margin-top:46px;font-size:30px}
.card-lead{margin:22px auto 0;width:340px;font-size:13.5px;line-height:1.6;color:var(--muted)}
.contact-row{display:flex;align-items:center;gap:14px;margin:26px 0 0 74px;text-align:left}
.contact-row .ico{flex:none;width:38px;height:38px;border-radius:50%;border:2px solid var(--teal);display:flex;align-items:center;justify-content:center}
.contact-row strong{display:block;font-weight:400;font-size:17px;line-height:1.3;color:var(--blue)}
.contact-row small{font-size:11.5px;color:var(--muted)}

/* footer */
.footer{position:absolute;left:0;top:4060px;width:1200px;height:175px}
.footer .brand{position:absolute;left:130px;top:98px;color:var(--white);font-size:30px}
.footer .brand .dot{background:var(--white)}
.social{position:absolute;left:494px;top:106px;display:flex;gap:14px}
.social span{width:38px;height:38px;border-radius:50%;border:2px solid var(--white)}
.copyright{position:absolute;left:880px;top:117px;font-size:12px;color:#e6f6f6}
</style>
</head>
<body>

<header class="hero">
  <div class="hero-photo" role="img" aria-label="Pale, misty photograph of a city skyline reflected in a river"></div>
  <div class="brand abs site-brand"><span class="dot"></span>Velqua</div>
  <nav class="nav">
    <a href="#about" style="left:482px">About</a>
    <a href="#solutions" class="active" style="left:620px">Solutions</a>
    <a href="#technology" style="left:782px">Technology</a>
    <a href="#products" style="left:943px">Products</a>
    <a href="#contact" style="left:1088px">Contact</a>
  </nav>
  <h1 class="abs hero-title">Advanced Oxidation Science</h1>
  <div class="abs hero-sub">for Environmental Pollution Management</div>
  <div class="abs scroll-cue">
    <svg width="32" height="32" viewBox="0 0 32 32"><path d="M10 13l6 6 6-6" fill="none" stroke="#2bb3b1" stroke-width="2.5"/></svg>
  </div>
  <svg class="abs" style="left:0;top:620px" width="1200" height="80" viewBox="0 0 1200 80" preserveAspectRatio="none">
    <path d="M0 30 C300 70 600 -5 900 25 C1040 40 1130 35 1200 20 L1200 80 L0 80Z" fill="#2bb3b1"/>
    <path d="M0 48 C300 85 620 15 900 42 C1040 55 1130 50 1200 40 L1200 80 L0 80Z" fill="#2f7fa8"/>
  </svg>
</header>

<section class="about" id="about">
  <h2 class="abs">About <span>Velqua</span></h2>
  <div class="abs about-copy">
    <p>Velqua develops advanced oxidation technologies and materials, which it licenses to Velqua Systems, China.</p>
    <p>Velqua Systems is engaged in the sales, service and support of environmental solutions for industry and government. With offices in Shanghai, Beijing, Shijiazhuang, and Chengdu, Velqua Systems is among the most advanced and rapidly growing companies offering solutions for air, water and fuel environmental compliance. Velqua Research Corporation supports these solutions with research and development.</p>
    <p>Velqua Research Corporation pursues business development opportunities in markets worldwide.</p>
  </div>
  <div class="photo-circle" role="img" aria-label="Photograph of an industrial treatment tower and plant" style="left:752px;top:90px;width:218px;height:218px;background:linear-gradient(180deg,#7fb6dc 0%,#a9b7bf 55%,#6e6c66 100%)"></div>
  <div class="photo-circle" role="img" aria-label="Photograph of red industrial filtration housings" style="left:918px;top:338px;width:172px;height:172px;background:linear-gradient(180deg,#8bb4d0 0%,#a44a3c 60%,#6a3a32 100%)"></div>
</section>

<section id="solutions">
  <h2 class="abs sec-title" style="top:1388px">Solutions</h2>
  <p class="abs sec-lead" style="top:1450px">Environmental pollution control solutions employing nature's most reactive Free Radical</p>

  <div class="solution" style="left:90px;top:1562px">
    <svg class="sol-icon" viewBox="0 0 124 124"><circle cx="62" cy="62" r="56" fill="none" stroke="#2bb3b1" stroke-width="7"/><path d="M62 30 C52 48 44 58 44 70 a18 18 0 0 0 36 0 C80 58 72 48 62 30Z" fill="#1b72c0"/></svg>
    <h3>Water</h3>
    <p>Clean water treatment with fast acting oxidation, ready for plant scale use and simple.</p>
    <a class="read-more" href="#">Read More</a>
  </div>
  <div class="solution" style="left:449px;top:1562px">
    <svg class="sol-icon" viewBox="0 0 124 124"><circle cx="62" cy="62" r="56" fill="none" stroke="#2bb3b1" stroke-width="7"/><circle cx="62" cy="62" r="6" fill="#1b72c0"/><path d="M62 56 C50 40 56 30 68 34 C74 40 70 50 62 56Z M67 65 C86 66 90 77 80 84 C72 84 66 76 67 65Z M56 65 C46 82 36 80 36 68 C40 62 48 60 56 65Z" fill="#1b72c0"/></svg>
    <h3>Air</h3>
    <p>Air emission control that removes harmful gases at the stack, with a low running cost.</p>
    <a class="read-more" href="#">Read More</a>
  </div>
  <div class="solution" style="left:807px;top:1562px">
    <svg class="sol-icon" viewBox="0 0 124 124"><circle cx="62" cy="62" r="56" fill="none" stroke="#2bb3b1" stroke-width="7"/><path d="M62 28 C72 44 82 52 80 70 a18 18 0 0 1 -36 0 C44 60 50 54 54 46 C56 54 60 56 62 56 C60 46 58 38 62 28Z" fill="#1b72c0"/><path d="M62 62 C68 70 70 76 68 82 a6 6 0 0 1 -12 0 C56 76 58 70 62 62Z" fill="#fff"/></svg>
    <h3>Fuel</h3>
    <p>Fuel upgrading that cuts sulfur and nitrogen content to meet the latest quality rules.</p>
    <a class="read-more" href="#">Read More</a>
  </div>
</section>

<section class="tech" id="technology">
  <div class="abs tech-photo" role="img" aria-label="Photograph of a technician in protective gear handling chemical drums"></div>
  <h2 class="abs">Advanced <span>Oxidation</span></h2>
  <div class="abs tech-copy">
    <p>Advanced Oxidation refers to a variety of techniques employing the Hydroxyl Radical, an energetic, highly reactive cousin of the water molecule:</p>
    <ul>
      <li>To add oxygen to inorganic molecules</li>
      <li>To remove hydrogen from organic molecules</li>
    </ul>
    <p>These transformations convert important industrial contaminants into reactive forms that can be captured or that disintegrate into harmless end products.</p>
  </div>
</section>

<section id="products">
  <h2 class="abs sec-title" style="top:2692px">Our <span>Products</span></h2>

  <div class="product" style="left:54px;top:2827px">
    <div class="prod-photo" role="img" aria-label="Photograph of a tall glass building against blue sky" style="background:linear-gradient(160deg,#b9dcf0 0%,#3a88c4 55%,#1b4f86 100%)"></div>
    <h3>GASOX</h3>
    <div class="full">Flue Gas Advanced<br>Oxidation Catalytic Process</div>
    <p>Stack gas treatment made<br>clean, quick and reliable.</p>
    <a class="read-more" href="#">Read More</a>
  </div>
  <div class="product" style="left:327px;top:2827px">
    <div class="prod-photo" role="img" aria-label="Photograph of solar panels under a purple sky" style="background:linear-gradient(180deg,#7f7fc6 0%,#5a70b8 45%,#2d4f8e 100%)"></div>
    <h3>SOLOX</h3>
    <div class="full">Photo Electric Advanced<br>Oxidation Catalytic Process</div>
    <p>Light driven treatment made<br>clean, quick and reliable.</p>
    <a class="read-more" href="#">Read More</a>
  </div>
  <div class="product" style="left:604px;top:2827px">
    <div class="prod-photo" role="img" aria-label="Photograph of an offshore oil platform at sunset" style="background:linear-gradient(180deg,#e8b07a 0%,#b8705a 50%,#3e3a48 100%)"></div>
    <h3>PETROX</h3>
    <div class="full">Petroleum Dehydrate Advanced<br>Oxidation Catalytic Process</div>
    <p>Fuel refining treatment made<br>clean, quick and reliable.</p>
    <a class="read-more" href="#">Read More</a>
  </div>
  <div class="product" style="left:878px;top:2827px">
    <div class="prod-photo" role="img" aria-label="Illustration of a small green tree growing from a light bulb" style="background:linear-gradient(180deg,#6fc2e6 0%,#2c8fc4 55%,#1a5b8a 100%)"></div>
    <h3>VAPOX</h3>
    <div class="full">Volatile Organic Compounds<br>Advanced Oxidation Catalytic</div>
    <p>Vapor control treatment made<br>clean, quick and reliable.</p>
    <a class="read-more" href="#">Read More</a>
  </div>
</section>

<section class="partners" aria-label="Partners">
  <div class="partner" style="left:92px">
    <div class="mark"><span class="ring"></span>Velqua Systems</div>
    <p>Sales Partner<br>in China</p>
  </div>
  <div class="partner" style="left:346px">
    <div class="mark">Pelmark Chemical</div>
    <p>Our construction<br>partner in China</p>
  </div>
  <div class="partner" style="left:614px">
    <div class="mark"><span class="seal"></span></div>
    <p>Technology partner<br>in China</p>
  </div>
  <div class="partner" style="left:883px">
    <div class="mark"><span class="seal"></span></div>
    <p>Technology partner<br>in China</p>
  </div>
</section>

<section id="contact">
  <div class="map" role="img" aria-label="Faint grey street map of the office neighbourhood"></div>
  <div class="card">
    <div class="brand"><span class="dot"></span>Velqua</div>
    <p class="card-lead">We welcome inquiries regarding the licensing, distribution, and purchase of our products, systems and technologies.</p>
    <div class="contact-row">
      <span class="ico"><svg width="18" height="18" viewBox="0 0 18 18"><rect x="5" y="2" width="8" height="14" rx="1.5" fill="none" stroke="#2bb3b1" stroke-width="1.6"/><circle cx="9" cy="13.2" r="0.9" fill="#2bb3b1"/></svg></span>
      <div><strong>+1-555-010-4821</strong><small>Office hours 8am – 5pm</small></div>
    </div>
    <div class="contact-row">
      <span class="ico"><svg width="18" height="18" viewBox="0 0 18 18"><rect x="2" y="4" width="14" height="10" rx="1" fill="none" stroke="#2bb3b1" stroke-width="1.6"/><path d="M2 5l7 5 7-5" fill="none" stroke="#2bb3b1" stroke-width="1.6"/></svg></span>
      <div><strong>info@velquaresearch.example</strong><small>We reply within a day</small></div>
    </div>
  </div>
</section>

<footer class="footer">
  <svg class="abs" style="left:0;top:0" width="1200" height="175" viewBox="0 0 1200 175" preserveAspectRatio="none">
    <path d="M0 40 C300 5 600 70 900 40 C1040 26 1130 30 1200 44 L1200 175 L0 175Z" fill="#7fd4d3"/>
    <path d="M0 60 C300 25 620 90 900 60 C1040 46 1130 50 1200 62 L1200 175 L0 175Z" fill="#2bb3b1"/>
  </svg>
  <div class="brand"><span class="dot"></span>Velqua</div>
  <div class="social" aria-label="Social links"><span></span><span></span><span></span></div>
  <p class="copyright">© 2016. Copyrights. All Rights Reserved</p>
</footer>

</body>
</html>
```